Red Mo's Wine Label Project

We need a new entry level wine label called "Red Mo's" for a range of wines we are developing from inland Australia. Our company is made up of three youngish guys who live hard and love taking the mickey. Red Mo is Red Morrie - the largest and loudest of the three partners (and ideally this label will take the mickey out of him). We've grown the grapes ourselves for this first release which will be a 2012 Pinot Gris. Wine style is dry, young, fresh and contemporary and pitched at the sub AUD $10 retail price point. The package will be flint (clear) claret shape bottle with plain screwcap (colour matched to suit the winning label design).

I've attached a couple of photos of Red Morrie to give you some idea of his presence and persona.

Target Market(s)

Semi educated 25 - 40 year old wine drinkers. Skewed towards females.

Industry/Entity Type

Retail

Requirements
Should not have
• Anything traditional or old fashioned

```html
<!DOCTYPE html>
<html lang="en">
<head>
<meta charset="UTF-8">
<title>Red Mo's Pinot Gris 2012 Label</title>
<link rel="stylesheet" href="https://fonts.googleapis.com/css2?family=Questrial&display=swap">
<style>
  :root {
    --backdrop: #f2f2f2;
    --label-white: #ffffff;
    --label-black: #231f20;
    --brand-crimson: #d8185a;
    --text-white: #ffffff;
  }
  * { margin: 0; padding: 0; box-sizing: border-box; }
  html, body {
    width: 1200px;
    height: 2520px;
    overflow: hidden;
    background: var(--backdrop);
  }
  .canvas {
    position: relative;
    width: 1200px;
    height: 2520px;
    display: flex;
    align-items: center;
    justify-content: center;
  }
  .wine-label {
    width: 1100px;
    height: 1880px;
    display: flex;
    flex-direction: column;
    font-family: "Questrial", "Century Gothic", sans-serif;
  }
  .brand-panel {
    height: 897px;
    background: var(--label-white);
    display: flex;
    align-items: center;
    justify-content: center;
    padding-top: 120px;
  }
  .brand-name {
    color: var(--brand-crimson);
    font-size: 290px;
    font-weight: 400;
    line-height: 1;
    letter-spacing: -4px;
    white-space: nowrap;
  }
  .details-panel {
    flex: 1;
    background: var(--label-black);
    color: var(--text-white);
    display: flex;
    flex-direction: column;
    align-items: center;
    padding-top: 60px;
    text-transform: uppercase;
    white-space: nowrap;
  }
  .varietal {
    font-size: 196px;
    line-height: 1;
    letter-spacing: 0;
  }
  .alcohol {
    margin-top: 30px;
    font-size: 146px;
    line-height: 1;
    letter-spacing: 0;
  }
  .vintage {
    margin-top: 30px;
    font-size: 460px;
    line-height: 1;
    letter-spacing: 2px;
  }
</style>
</head>
<body>
  <main class="canvas">
    <article class="wine-label">
      <header class="brand-panel">
        <h1 class="brand-name">Red Mo</h1>
      </header>
      <section class="details-panel">
        <p class="varietal">Pinot Gris</p>
        <p class="alcohol">Alkohol 12%</p>
        <p class="vintage">2012</p>
      </section>
    </article>
  </main>
</body>
</html>
```